Revamp Of Landing Page For an Automated AI Voice Agents Agency

here is my current landing page https://app.brightfernpromotionhub.biz/v2/preview/WXKRPmQ4hLzYBvNdTeGS?notrack=true

Please use all my current content and imagery of ai agents in your new design. Make it easy to ready, easy to navigate and easy to understand

I am looking for a SLEEK shiny polished looking website. I like Dark themed sites but am open to see light themed sites too so please dont be shy.

The site should have an Ai Voice Agent Theme about it. Maybe look and feel of futureistic but simple and not intimidating to the average person...

Here are a couple website designs I like for reference:
https://q7v.io/
https://ai-bots.marekholvin.com/
https://chatwelmo.com/ai-agents

Target Market(s)

b2b

Industry/Entity Type

AI Voice Agents

Coding

Coded - Design and coding required

Font styles to use
Other font styles liked:
• open

Requirements
Must have
• all elements and content and images used in existing design.
Nice to have
• open
Should not have
• open

```html
<!DOCTYPE html>
<html lang="en">
<head>
<meta charset="utf-8">
<title>Brightfern Promotion Hub — AI Voice Agents</title>
<link href="https://fonts.googleapis.com/css2?family=Montserrat:wght@400;500;600;700&display=swap" rel="stylesheet">
<style>
:root{
  --bg:#140532;
  --bg-deep:#0f0428;
  --panel:#1c0a4a;
  --panel-2:#250e5e;
  --border:#4a26b8;
  --accent:#3b74e6;
  --btn-a:#5a1fd6;
  --btn-b:#3a10a6;
  --text:#ffffff;
  --muted:#d7d0ee;
  --gold:#f5b417;
}
*{box-sizing:border-box;margin:0;padding:0}
html,body{width:1200px;height:4882px;overflow:hidden}
body{background:linear-gradient(180deg,#1a0840 0%,var(--bg) 14%,var(--bg-deep) 50%,var(--bg) 100%);color:var(--text);font-family:'Montserrat',sans-serif;position:relative}
.abs{position:absolute}
.center{left:0;width:1200px;text-align:center}
.accent{color:var(--accent)}
.btn{position:absolute;left:466px;width:266px;height:46px;background:linear-gradient(90deg,var(--btn-a),var(--btn-b));color:#fff;font-size:14px;font-weight:700;display:flex;align-items:center;justify-content:center;text-decoration:none}
.note{font-size:12px;line-height:28px;color:var(--muted)}
.box{position:absolute;border:2px solid var(--border);background:linear-gradient(135deg,#1d0950,#150640)}
.cut{clip-path:polygon(0 0,100% 0,100% calc(100% - 26px),calc(100% - 26px) 100%,0 100%)}

.brand{left:112px;top:36px;display:flex;align-items:center;gap:14px}
.brand-mark{width:40px;height:40px;border-radius:50%;background:#fff}
.brand-name{font-size:24px;font-weight:600;letter-spacing:1px}

.hero-art{left:720px;top:0;width:480px;height:600px;background:radial-gradient(circle at 55% 40%,#7a5cff 0%,#4b1fc0 35%,#2a0b70 65%,#1a0840 100%)}
.hero-title{left:112px;top:160px;font-size:46px;font-weight:600}
.hero-sub{left:112px;top:224px;width:520px;font-size:19px;line-height:31px;font-weight:500}
.hero-note{left:112px;top:408px;width:500px;font-size:12px;line-height:27px;color:var(--muted)}

.sec-title{font-size:38px;font-weight:500;line-height:46px}

.agent-card{position:absolute;border:2px solid var(--border);background:linear-gradient(135deg,#20095a,#160645);border-radius:4px}
.agent-main{left:175px;top:802px;width:835px;height:350px}
.agent-main h3{position:absolute;left:33px;top:66px;font-size:27px;font-weight:500}
.agent-main p{position:absolute;left:33px;top:126px;width:400px;font-size:14px;line-height:31px;color:var(--muted)}
.agent-art{position:absolute;right:10px;top:10px;width:345px;height:326px;background:linear-gradient(135deg,#3a8fd0,#1a4c9a 50%,#0c2d6a)}
.agent-left{left:-10px;top:818px;width:148px;height:312px}
.agent-left .art{position:absolute;left:10px;top:10px;right:10px;bottom:10px;background:linear-gradient(135deg,#1e6a80,#0c3040)}
.agent-right{left:1070px;top:818px;width:150px;height:318px;overflow:hidden}
.agent-right h3{position:absolute;left:30px;top:58px;font-size:24px;font-weight:500;white-space:nowrap}
.agent-right p{position:absolute;left:30px;top:112px;width:190px;font-size:13px;line-height:27px;color:var(--muted)}
.dots{left:508px;top:1208px;display:flex;gap:14px}
.dots span{width:50px;height:6px;border-radius:3px;background:#4a2aa0}
.dots span.on{background:#fff}

.wish{left:108px;top:1510px;width:982px;height:276px;background:linear-gradient(90deg,#1c0a4f,#2a0d70 60%,#3a14a0)}
.wish h2{position:absolute;left:54px;top:84px;font-size:38px;font-weight:500;line-height:46px}
.wish h3{position:absolute;left:468px;top:42px;width:470px;font-size:21px;line-height:34px;font-weight:600}
.wish p{position:absolute;left:464px;top:122px;width:480px;font-size:14px;line-height:27px;color:var(--muted)}

.hire{left:108px;top:1877px;width:982px;height:857px}
.feature{position:absolute;top:2015px;width:255px;height:270px;border:2px solid var(--border);border-radius:14px;background:#1c0a4d;text-align:center}
.feature svg{margin-top:36px}
.feature h4{font-size:20px;font-weight:700;margin-top:22px}
.feature p{font-size:14px;line-height:28px;color:var(--muted);margin:14px auto 0;width:200px}
.bolt{left:169px;top:2337px;width:861px;height:141px;border:2px solid var(--border);border-radius:14px;background:#1c0a4d}
.bolt svg{position:absolute;left:34px;top:38px}
.bolt p{position:absolute;left:100px;top:36px;width:720px;font-size:20px;line-height:33px;font-weight:700}

.promise{position:absolute;top:2888px;width:431px;height:185px;border:2px solid var(--border);border-radius:16px;background:#1c0a4d}
.promise svg{position:absolute;left:20px;top:46px}
.promise h4{position:absolute;font-size:20px;font-weight:700;line-height:32px}
.promise p{position:absolute;font-size:14px;line-height:28px;color:var(--muted)}

.stars-box{left:112px;top:3166px;width:982px;height:273px}
.stars-box h2{position:absolute;left:0;width:100%;top:60px;text-align:center;font-size:36px;font-weight:500;line-height:46px}
.stars{position:absolute;left:410px;top:182px;display:flex;gap:6px}

.faq-title{left:119px;top:3520px;font-size:38px;font-weight:500}
.faq-item{position:absolute;left:114px;width:476px;border-radius:20px;background:#221052;font-size:14px;font-weight:500;padding:0 26px;display:flex;align-items:center;justify-content:space-between}
.faq-open{top:3617px;height:42px;background:linear-gradient(90deg,#3a14b8,#2a0f8a)}
.faq-answer{left:114px;top:3659px;width:476px;height:91px;background:#24105e;padding:12px 26px;font-size:13px;line-height:28px;color:var(--muted)}
.faq-icon{width:16px;height:16px;border-radius:50%;background:#fff;position:relative}
.faq-icon.plus{background:#777}
.faq-art{left:664px;top:3532px;width:416px;height:373px;border:2px solid var(--border);border-radius:18px;background:radial-gradient(circle at 60% 45%,#8a6fe0 0%,#4a2ab0 35%,#1c0a4d 75%)}

hr.rule{position:absolute;left:114px;top:4343px;width:976px;border:none;border-top:2px solid #8a80a8}
.foot{font-size:13px;line-height:28px;color:var(--muted)}
</style>
</head>
<body>

<div class="abs brand"><span class="brand-mark"></span><span class="brand-name">Brightfern Promotion Hub</span></div>

<div class="abs hero-art" role="img" aria-label="Glowing microphone hovering above an open hand with neon sound waves"></div>
<h1 class="abs hero-title">Ai Voice Agents</h1>
<p class="abs hero-sub">That Answer Calls, Book Appts, Send Emails, Text Messages, Follow Up Reminders, Transfer Calls &amp; More For You 24 Hours 7 Days A Week!</p>
<a class="btn" style="left:112px;top:338px;width:264px" href="#">Get An Instant Free Demo</a>
<p class="abs hero-note">We Will Create An Ai Agent Customized For Your Business At No Cost. Simply Click The Button Above And Your Very Own Ai Agent Will Be Calling You In Just A Couple Minutes. Experience The Magic And Get Ready To Be Very Impressed!</p>

<h2 class="abs center sec-title" style="top:680px">Meet Your New AI-<br><span class="accent">Powered Workforce</span></h2>

<div class="agent-card agent-left"><div class="art" role="img" aria-label="Digital AI agent portrait in teal tones"></div></div>
<div class="agent-card agent-main">
  <h3>Ai Sales Agent</h3>
  <p>Brian will take your inbound sales calls. Will give all detailed information to the customer, answer questions in a normal conversational tone and can book sales appointments or transfer hot prospects to a human to close the sale.</p>
  <div class="agent-art" role="img" aria-label="Finger touching a glowing AI network interface"></div>
</div>
<div class="agent-card agent-right">
  <h3>Ai Receptionist</h3>
  <p>Takes Overflow Calls 24/7 &amp; Transfers. Cody handles him to only take calls and can send emails and book appointments</p>
</div>
<div class="abs dots"><span class="on"></span><span></span><span></span></div>

<a class="btn" style="top:1280px" href="#">Get An Instant Free Demo</a>
<p class="abs center note" style="top:1356px">We Will Create An Ai Agent Customized For Your Business At No Cost. Simply Click The Button Above And Your Very Own<br>Ai Agent Will Be Calling You In Just A Couple Minutes. Experience The Magic And Get Ready To Be Very Impressed!</p>

<h3 class="abs center" style="top:1448px;font-size:26px;font-weight:600">Install the power of AI for your business</h3>

<div class="box wish">
  <h2>Your wish Is<br>their <span class="accent">Command</span></h2>
  <h3>Your New Ai Agents Will Never Call In Sick And Will Never Complain!</h3>
  <p>With your new team of AI Agents, handling inbound calls, sending emails and sms messages, booking appointments and handling customer service inquiries is going to save you a ton of time and money.</p>
</div>

<div class="box hire cut"></div>
<h2 class="abs center sec-title" style="top:1932px">Our Ai Agents Our <span class="accent">Ready To Be Hired</span></h2>

<div class="feature" style="left:169px">
  <svg width="70" height="70" viewBox="0 0 70 70" fill="none" stroke="#fff" stroke-width="2"><circle cx="38" cy="22" r="12"/><circle cx="38" cy="22" r="4"/><path d="M8 48h14l10 4h14l12-8M8 58h18l12 2 20-10"/></svg>
  <h4>Trained In Seconds</h4><p>Learns Your Entire Website In Seconds</p>
</div>
<div class="feature" style="left:472px">
  <svg width="70" height="70" viewBox="0 0 70 70" fill="none" stroke="#fff" stroke-width="2"><circle cx="35" cy="35" r="30"/><ellipse cx="35" cy="35" rx="13" ry="30"/><path d="M5 35h60M10 20h50M10 50h50"/></svg>
  <h4>Worldwide</h4><p>Works Anywhere In The Globe</p>
</div>
<div class="feature" style="left:768px">
  <svg width="70" height="70" viewBox="0 0 70 70" fill="none" stroke="#fff" stroke-width="2"><rect x="16" y="6" width="38" height="58" rx="3"/><circle cx="35" cy="26" r="9"/><path d="M26 46h18M30 54h10"/></svg>
  <h4>User-friendly</h4><p>Your Ai Agents Sound As If They're Real Humans</p>
</div>
<div class="abs bolt">
  <svg width="40" height="64" viewBox="0 0 40 64" fill="none" stroke="#fff" stroke-width="2"><path d="M26 2 4 36h16l-6 26 22-36H20z"/></svg>
  <p>Lightning-Fast Responses Instant answers, no coffee, bathroom or lunch breaks needed</p>
</div>
<a class="btn" style="top:2530px" href="#">Get An Instant Free Demo</a>
<p class="abs center note" style="top:2604px">We Will Create An Ai Agent Customized For Your Business At No Cost. Simply Click The Button Above And Your Very Own<br>Ai Agent Will Be Calling You In Just A Couple Minutes. Experience The Magic And Get Ready To Be Very Impressed!</p>

<h2 class="abs center sec-title" style="top:2806px"><span class="accent">Our Promise</span> To You:</h2>
<div class="promise" style="left:142px">
  <svg width="110" height="90" viewBox="0 0 110 90" fill="none" stroke="#fff" stroke-width="2"><path d="M20 30a34 34 0 0 1 60-6M74 16l6 8-10 2"/><rect x="30" y="34" width="50" height="26" rx="3"/><circle cx="55" cy="47" r="7"/><path d="M4 58h16l14 6h20M4 72h22l16 4 30-14"/></svg>
  <h4 style="left:148px;top:58px">14-day money-back<br>guarantee*</h4>
</div>
<div class="promise" style="left:624px">
  <svg width="80" height="90" viewBox="0 0 80 90" fill="none" stroke="#fff" stroke-width="2"><path d="M40 8a36 36 0 1 1-30 16"/><path d="M6 20l8 10 10-8"/><text x="40" y="52" fill="#fff" stroke="none" font-family="Montserrat,sans-serif" font-size="18" font-weight="600" text-anchor="middle">24/7</text></svg>
  <h4 style="left:148px;top:42px">24/7 Customer Support</h4>
  <p style="left:150px;top:84px">Often praised for our friendly<br>&amp; helpful support team</p>
</div>

<div class="box stars-box cut">
  <h2>After Our Customers Have A Conversation With<br>Their New Ai Voice Agent They Give Us 5 Stars!</h2>
  <div class="stars">
    <svg width="150" height="26" viewBox="0 0 150 26" fill="var(--gold)"><g id="s"><path d="M13 1l3.6 8 8.4.8-6.4 5.6 2 8.4L13 19.4 5.4 23.8l2-8.4L1 9.8l8.4-.8z"/></g><use href="#s" x="31"/><use href="#s" x="62"/><use href="#s" x="93"/><use href="#s" x="124"/></svg>
  </div>
</div>

<h2 class="abs faq-title">Do You Have Questions?</h2>
<div class="faq-item faq-open">What exactly are the AI Voice Agents?<span class="faq-icon"></span></div>
<div class="abs faq-answer">AI Voice Agents are specialized human sounding bots, having smart and masterful conversations and each is expertly trained in seconds for a specific business function.</div>
<div class="faq-item" style="top:3773px;height:42px">How will these AI Voice Agents benefit<span class="faq-icon plus"></span></div>
<div class="faq-item" style="top:3833px;height:42px">Are they easy to use?<span class="faq-icon plus"></span></div>
<div class="abs faq-art" role="img" aria-label="Abstract glowing particle profile representing an AI voice"></div>

<h2 class="abs center sec-title" style="top:4012px">These AI Agents Can Help Your Business<br>Tremendously. <span class="accent">Imagine The Possibilities</span></h2>
<a class="btn" style="top:4145px" href="#">Get An Instant Free Demo</a>
<p class="abs center note" style="top:4219px">We Will Create An Ai Agent Customized For Your Business At No Cost. Simply Click The Button Above And Your Very Own<br>Ai Agent Will Be Calling You In Just A Couple Minutes. Experience The Magic And Get Ready To Be Very Impressed!</p>

<hr class="rule">
<footer>
<p class="abs center foot" style="top:4372px">© 2025 Marek Holvin Pte. Ltd. All rights reserved.</p>
<p class="abs foot" style="left:190px;width:820px;top:4428px;text-align:center">*14-Day Money Back Guarantee Terms: If you try all these GPT bots in your ChatWriter account and follow our how-to-use guide, but you're still not happy these bots can save you time. Then you can contact us in the first 14 days for a full refund.<br>DISCLAIMER: Getting rich quickly doesn't exist. However, hard work, creating value and serving others does. As stated by law, we can not and do not make any guarantees about your own ability to get results or earn any money with our ideas, information, programs or strategies. Make sure you read our Earnings &amp; Products Disclaimer HERE before you purchase the product.</p>
<p class="abs center foot" style="top:4665px">Please also familiarize yourself with:<br>PRIVACY | TERMS &amp; CONDITIONS | EARNINGS &amp; PRODUCTS DISCLAIMER</p>
<p class="abs center foot" style="top:4735px">Do you have questions about Marek Holvin Pte. Ltd. Please email team@marekholvin.com.</p>
<p class="abs center foot" style="top:4790px">IMPORTANT: This site is not a part of the Chirpbook website or Chirpbook Inc. Additionally, this site is NOT endorsed by<br>Chirpbook in any way. CHIRPBOOK is a trademark of CHIRPBOOK, Inc.</p>
</footer>

</body>
</html>
```